Lotstallmart.com Webpage Design

Design Brief for lotstallmart.com (Copy of Brief also in attached Word file)

Name of Website- lotstallmart.com (existing logo and look & feel of website to be changed)

Logo - Finalised. The logo files are attached with the brief as “logo.jpeg”. The “Blue- Grey” version of the logo is for use on lighter backgrounds and the “Orange-White” version of the logo is for use on darker backgrounds. (A full Black version of the logo is also attached). Both versions may be used in different parts of the website. All attached files are in .png format.
Status - The website in functional and is undergoing user trials. However, we want to improve the look & feel of the website so at it seems
a. cotemporary,
b. Easy to Navigate
c. professional and
d. Vibrant.

Please visit ‘lotstallmart.com’ to check out the website and its functionalities – please use it only as a reference for the features & functions to be provided, however the designer should use a ‘Free Hand’ in designing the composition of various parts of the webpage without getting too influenced by the existing design

Objective of the Website ‘lotstallmart.com –
a. It is a portal focussed on listing of ‘Retail’ specific real-estate properties by developers, owners and realty brokers. The properties shall listed under the following four categories-
i. Retail Malls
ii. Shopping Complexes
iii. High-street shops
iv. Retail Warehouses
*refer lotstallmart.com for better clarity

b. The abovementioned properties shall be listed either for ‘Sale’ or ‘rent\lease’ or both

c. Users shall visit the site in case they wish to acquire a retail \ shop space either on ‘sale’ or ‘rent’. These Users would be able to specify the ‘Search Criteria’ through the tool-bars provided on the website – the ‘Search Criteria’ shall comprise of ‘Type of space category’, ‘City’, ‘Locality’, transaction type ie ‘Rent \ Sale’ and ‘Area Range’

d. The main revenue model for the website shall be listing fee ( or advertising charges ) payable by those listing their properties on the website.

Three Main Pages of Website (lotstallmart.com) that need to be designed -
a. Main Home Page (visit the web link - http://lotstallmart.com/ ) - The main home page has the “Search Toolbar” for specifying of Search Criteria by the User. It shall also have the following features & functions-
i. Main Advertising Banner
ii. Featured Projects
iii. New Launches
iv. Toolbar with buttons – ‘Advertise with Us’, ‘Listings Alert’, ‘Mart Wizards’, ‘Advertiser Login’

b. Property Listings Page (visit the web link - http://lotstallmart.com/gurgaon-in-india ) - The List of property options that match the Criteria specified by the ‘User’ get displayed on this page.

c. Property Detail Page - When the ‘User’ clicks on the “More….” Button on the ‘Property Listings Page’ (given in point b. above) the web page with the details of the property opens. (For Example – visit the web link - http://lotstallmart.com/vorne-Shopping-Complex-vorne-quadrion-gurgaon-636 )

Note:- Please refer to attached ‘Shopping’ related images the designer may use them on the website to provide a look & feel of retail if required – either separately or rotate in a single window

Target Market(s)

Retailers & Investors looking for retail space, Real Estate Brokers, Developers

Industry/Entity Type

Advertising

Number of Pages Required

3 page

Requirements
Must have
• Refer to existing site lotstallmart.com -- all the existing functionalities are a must have.
Nice to have
• The Designer may use the retail related images on the website if required for making it more vibrant. Refer attached images Shopping(1-6).jpg

```html
<!DOCTYPE html>
<html lang="en">
<head>
<meta charset="utf-8">
<title>lotstallmart.com</title>
<link rel="stylesheet" href="https://fonts.googleapis.com/css2?family=Ubuntu:wght@400;500;700&family=Open+Sans:wght@400;600;700&display=swap">
<style>
:root{
  --blue:#0b8fe3;
  --blue-dark:#0a6fc2;
  --blue-btn:#1487d6;
  --grey-btn:#6b6d70;
  --ink:#222;
  --muted:#666;
  --red:#c0392b;
  --footer:#454545;
  --card-bg:#f6f6f6;
  --line:#ddd;
}
*{box-sizing:border-box;margin:0;padding:0}
html,body{width:738px;height:1200px;overflow:hidden;background:#fff}
body{position:relative;font-family:"Open Sans",sans-serif;color:var(--ink)}
.abs{position:absolute}

.topbar{left:0;top:0;width:738px;height:28px;background:var(--blue)}
.topbar .call{left:70px;top:8px;font-size:7px;font-weight:700;color:#fff}
.topbar .social{left:504px;top:9px;display:flex;gap:5px}
.topbar .social span{width:9px;height:9px;border-radius:50%;background:#fff;opacity:.9}
.city{left:587px;top:0;width:80px;height:28px;background:var(--blue-dark);color:#fff;font-size:8px;font-weight:600;display:flex;align-items:center;justify-content:center;gap:4px}

.header{left:0;top:28px;width:738px;height:58px;background:#fff}
.brand{left:70px;top:43px;display:flex;align-items:center;gap:6px}
.brand .mark{width:22px;height:22px;border-radius:50%;background:var(--blue)}
.brand .name{font-family:"Ubuntu",sans-serif;font-size:19px;font-weight:500;color:var(--blue-dark)}
.brand-tag{left:98px;top:66px;font-size:4.5px;font-weight:700;color:var(--muted);letter-spacing:.3px}
.home{left:291px;top:47px;width:21px;height:21px;border-radius:50%;background:var(--blue)}
.nav-item{font-family:"Ubuntu",sans-serif;font-size:8px;color:var(--blue)}
.nav-item small{display:block;font-size:6.5px;color:var(--ink);margin-top:2px}
.login{left:558px;top:43px;width:109px;height:25px;border-radius:3px;background:var(--blue);color:#fff;font-family:"Ubuntu",sans-serif;font-size:8.5px;display:flex;align-items:center;justify-content:center}

.hero{left:0;top:86px;width:738px;height:355px;background:linear-gradient(160deg,#5a4632 0%,#2f2a26 45%,#6d5a45 75%,#3a2e24 100%)}
.arrow{width:25px;height:25px;border-radius:50%;background:#fff;top:232px}
.dots{left:348px;top:424px;display:flex;gap:5px}
.dots span{width:8px;height:8px;border-radius:50%;background:#fff}
.dots span.on{background:#6cc04a}

.search{left:490px;top:134px;width:176px;height:265px;background:#fff}
.search-head{height:36px;background:var(--blue);color:#fff;font-family:"Ubuntu",sans-serif;font-size:10px;font-weight:500;padding:12px 11px}
.search label{position:absolute;left:11px;font-size:7px;color:#333}
.select{position:absolute;left:11px;width:155px;height:21px;border:1px solid #cfcfcf;font-size:6.5px;color:#666;padding:6px 5px}
.select::after{content:"";position:absolute;right:6px;top:8px;border:3px solid transparent;border-top:4px solid #888}
.submit{position:absolute;left:11px;top:214px;width:155px;height:27px;background:var(--grey-btn);color:#fff;font-size:7px;display:flex;align-items:center;justify-content:center}

.cat{top:462px;width:142px;height:54px;border-radius:2px;background:var(--blue-btn);color:#fff;text-align:center;font-family:"Ubuntu",sans-serif;font-size:11px;padding-top:13px}
.cat small{display:block;font-size:7.5px;margin-top:4px}
.cat.active{background:var(--grey-btn)}

.section-title{left:70px;font-family:"Ubuntu",sans-serif;font-size:14px;color:#555}
.section-title b{font-weight:400;color:var(--blue-dark)}

.card{width:140px;height:188px;background:var(--card-bg);border:1px solid var(--line)}
.card .photo{height:104px}
.card .tag{position:absolute;right:0;top:0;background:var(--blue);color:#fff;font-size:7px;font-weight:600;padding:3px 6px}
.card h3{font-size:8.5px;font-weight:400;margin:9px 6px 4px}
.card p{font-size:6.3px;line-height:11px;color:var(--muted);margin:0 6px}
.card .more{position:absolute;right:8px;bottom:12px;font-size:6.3px;font-style:italic;color:var(--red)}

.side-btn{left:524px;width:142px;height:54px;border-radius:2px;background:var(--blue-btn);color:#fff;font-family:"Ubuntu",sans-serif;font-size:11px;display:flex;align-items:center;justify-content:center}

.footer{left:0;top:1032px;width:738px;height:111px;background:var(--footer);color:#fff}
.fcol{top:1043px;font-size:6.5px;line-height:15px}
.fcol h4{font-family:"Ubuntu",sans-serif;font-size:9px;font-weight:500;margin-bottom:6px}
.fsocial{display:flex;gap:5px}
.fsocial span{width:15px;height:15px;border-radius:2px;background:#3a8fd8}
.fsocial span:last-child{background:#f08a24}
.bottombar{left:0;top:1143px;width:738px;height:57px;background:var(--blue);color:#fff;font-size:7.5px;font-weight:600;display:flex;align-items:center;justify-content:center}
</style>
</head>
<body>

<div class="abs topbar">
  <div class="abs call">CALL US: 0123 987 654</div>
  <div class="abs social"><span></span><span></span><span></span><span></span><span></span></div>
</div>
<div class="abs city">Bangalore <svg width="6" height="5" viewBox="0 0 6 5"><path d="M0.5 1 L3 3.5 L5.5 1" stroke="#fff" stroke-width="1.3" fill="none"/></svg></div>

<div class="abs header"></div>
<div class="abs brand"><span class="mark"></span><span class="name">lotstallmart</span></div>
<div class="abs brand-tag">INDIA'S LEADING PORTAL FOR RETAIL SPACE</div>
<div class="abs home"><svg width="21" height="21" viewBox="0 0 21 21"><path d="M6 11 L10.5 6.5 L15 11 M7.5 10 V14.5 H13.5 V10" stroke="#fff" stroke-width="1.6" fill="none"/></svg></div>
<div class="abs nav-item" style="left:325px;top:47px">Advertise with us<small>Standard listing - FREEShop</small></div>
<div class="abs nav-item" style="left:424px;top:47px">Mart Wizards<small>Shop Search Services</small></div>
<div class="abs nav-item" style="left:504px;top:53px">Listing Alert</div>
<div class="abs login">Advertiser Login</div>

<div class="abs hero" role="img" aria-label="Photo of a smiling family walking with shopping bags through a lit shopping arcade"></div>
<div class="abs arrow" style="left:21px"><svg width="25" height="25" viewBox="0 0 25 25"><path d="M14.5 7.5 L9.5 12.5 L14.5 17.5" stroke="#222" stroke-width="2.2" fill="none"/></svg></div>
<div class="abs arrow" style="left:688px"><svg width="25" height="25" viewBox="0 0 25 25"><path d="M10.5 7.5 L15.5 12.5 L10.5 17.5" stroke="#222" stroke-width="2.2" fill="none"/></svg></div>
<div class="abs dots"><span class="on"></span><span></span><span></span></div>

<form class="abs search">
  <div class="search-head">Select Retail Format:</div>
  <label style="top:50px">Sale Or Rent Or Both:</label>
  <div class="select" style="top:69px">Both</div>
  <label style="top:106px">Select City:</label>
  <div class="select" style="top:124px">--Select--</div>
  <label style="top:158px">Select Locality/Micro-Market.</label>
  <div class="select" style="top:177px">--Select--</div>
  <div class="submit">Submit</div>
</form>

<div class="abs cat active" style="left:70px">Retail Malls<small>Centrally Air-Conditioned</small></div>
<div class="abs cat" style="left:222px">Shopping Complex<small>Non Air-Conditioned Building</small></div>
<div class="abs cat" style="left:373px">High Street Shops<small>Road Facing Retail</small></div>
<div class="abs cat" style="left:524px">Retail Warehouses<small>Back-end Ratail Storage</small></div>

<div class="abs section-title" style="top:546px"><b>Featured</b> Projects</div>

<div class="abs card" style="left:70px;top:576px"><div class="photo" role="img" aria-label="Photo of women with shopping bags on an escalator" style="background:linear-gradient(135deg,#b9a58e,#5b4a3c)"></div><span class="tag">Surat</span><h3>Lorem Ipsum dollar</h3><p>Lorem ipsum dolor sit amet, consec-tetur adipisicing elit. Ullam volup-tate, accusamus</p><span class="more">-Readmore...</span></div>
<div class="abs card" style="left:222px;top:576px"><div class="photo" role="img" aria-label="Photo of a family shopping beside a sale sign" style="background:linear-gradient(135deg,#c9a24a,#8a5a2c)"></div><span class="tag">Surat</span><h3>Lorem Ipsum dollar</h3><p>Lorem ipsum dolor sit amet, consec-tetur adipisicing elit. Ullam volup-tate, accusamus</p><span class="more">-Readmore...</span></div>
<div class="abs card" style="left:375px;top:576px"><div class="photo" role="img" aria-label="Photo of a happy shopper holding colourful bags in a mall" style="background:linear-gradient(135deg,#d8d2c4,#a08e6c)"></div><span class="tag">Surat</span><h3>Lorem Ipsum dollar</h3><p>Lorem ipsum dolor sit amet, consec-tetur adipisicing elit. Ullam volup-tate, accusamus</p><span class="more">-Readmore...</span></div>
<div class="abs card" style="left:527px;top:576px"><div class="photo" role="img" aria-label="Photo of a bright shopping mall corridor" style="background:linear-gradient(135deg,#d6b27a,#7a5a3a)"></div><span class="tag">Surat</span><h3>Lorem Ipsum dollar</h3><p>Lorem ipsum dolor sit amet, consec-tetur adipisicing elit. Ullam volup-tate, accusamus</p><span class="more">-Readmore...</span></div>

<div class="abs section-title" style="top:787px"><b>New</b> Launches</div>

<div class="abs card" style="left:70px;top:817px;border-top:2px solid var(--blue)"><div class="photo" role="img" aria-label="Photo of shoppers in a festive mall atrium with balloons" style="background:linear-gradient(135deg,#d8a0b0,#8a6a5a)"></div><h3>Lorem Ipsum dollar</h3><p>Lorem ipsum dolor sit amet, consec-tetur adipisicing elit. Ullam volup-tate, accusamus</p><span class="more">-Readmore...</span></div>
<div class="abs card" style="left:222px;top:817px;border-top:2px solid var(--blue)"><div class="photo" role="img" aria-label="Photo of a multi-level mall interior with an atrium display" style="background:linear-gradient(135deg,#9a7a70,#3c4a6a)"></div><h3>Lorem Ipsum dollar</h3><p>Lorem ipsum dolor sit amet, consec-tetur adipisicing elit. Ullam volup-tate, accusamus</p><span class="more">-Readmore...</span></div>
<div class="abs card" style="left:375px;top:817px;border-top:2px solid var(--blue)"><div class="photo" role="img" aria-label="Photo of a modern mall with escalators and shop fronts" style="background:linear-gradient(135deg,#c8c8c4,#7a7a80)"></div><h3>Lorem Ipsum dollar</h3><p>Lorem ipsum dolor sit amet, consec-tetur adipisicing elit. Ullam volup-tate, accusamus</p><span class="more">-Readmore...</span></div>

<div class="abs side-btn" style="top:817px">Advertise with Us</div>
<div class="abs side-btn" style="top:885px">Listings Alert</div>
<div class="abs side-btn" style="top:951px">Mart Wizards</div>

<div class="abs footer"></div>
<div class="abs fcol" style="left:70px;color:#fff"><h4>About Us</h4>Home<br>Our Team<br>Our Work<br>Insight Articles<br>News</div>
<div class="abs fcol" style="left:178px;color:#fff"><h4>Our Services</h4>Brand &amp; Product Positioning<br>System 1 Research<br>Innovation<br>Hispanic Marketing</div>
<div class="abs fcol" style="left:371px;color:#fff"><h4>Contact Us Today</h4>Plot 12, Norvale Lane, Eastbrook.<br>P. O BOX 40117, Westmere.<br>m: +256 700 555 019<br>w: tallmartmedia.com<br>e: hello@tallmartmedia.com</div>
<div class="abs fcol" style="left:592px;color:#fff"><h4>Follow Us</h4><div class="fsocial"><span></span><span></span><span></span><span></span></div></div>

<div class="abs bottombar">© 2014 Lotstallmart.com - All Rights Reserved</div>

</body>
</html>
```